The Brighter Living Hour with Dan Kessop.

I'm launching this podcast on health and wellness and I want to be take serious. That starts with a great design. There's too much contradiction out there about what is and isn't healthy. I want my podcast to be a resource that people can rely upon. I want my face in it and I want it to pop with colors that catch the eye. I want It clean and crisp. I was also thinking of experimenting with an animated photo of me as well. What ever looks best.

Industry/Entity Type

Health And Wellness

Font styles to use
Sans Serif

Requirements
Must have
• My face and or body.

```html
<!DOCTYPE html>
<html lang="en">
<head>
<meta charset="utf-8">
<title>The Brighter Living Hour with Dan Kessop</title>
<link rel="stylesheet" href="https://fonts.googleapis.com/css2?family=Oswald:wght@400;700&display=swap">
<style>
  :root {
    --teal: #2e7d88;
    --teal-light: #3f8f97;
    --blue: #2b5d82;
    --navy: #1e2845;
    --ink: #1b2030;
    --white: #ffffff;
    --blush: #ebc4b6;
    --skin-light: #d99a72;
    --skin-dark: #a8653f;
    --denim: #35486a;
  }
  html, body {
    margin: 0;
    padding: 0;
    width: 1200px;
    height: 1200px;
    overflow: hidden;
    background: var(--navy);
  }
  .cover {
    position: relative;
    width: 1200px;
    height: 1200px;
    overflow: hidden;
    font-family: "Oswald", "Arial Narrow", sans-serif;
    background:
      radial-gradient(ellipse at 15% 20%, var(--teal-light) 0%, transparent 55%),
      radial-gradient(ellipse at 90% 95%, var(--ink) 0%, transparent 55%),
      linear-gradient(135deg, var(--teal) 0%, var(--blue) 50%, var(--navy) 100%);
  }
  .host-photo {
    position: absolute;
    left: 0;
    top: 0;
    width: 700px;
    height: 1200px;
    background:
      linear-gradient(90deg, rgba(46,125,136,0) 70%, rgba(43,93,130,1) 100%),
      linear-gradient(180deg, #3a3030 0%, var(--skin-light) 12%, var(--skin-dark) 55%, var(--skin-light) 85%, var(--denim) 88%, var(--denim) 100%);
    opacity: 0.92;
  }
  .title {
    position: absolute;
    left: 0;
    top: 0;
    width: 1200px;
    height: 1200px;
  }
  .title text { font-family: "Oswald", "Arial Narrow", sans-serif; font-weight: 700; }
  .word-white { fill: var(--white); }
  .word-blush { fill: var(--blush); }
  .word-light { font-weight: 400 !important; }
  .rule { fill: var(--blush); }
</style>
</head>
<body>
  <main class="cover">
    <div class="host-photo" role="img" aria-label="Photo of host Dan Kessop, shirtless in jeans, standing on the left side of the cover"></div>

    <svg class="title" viewBox="0 0 1200 1200" role="img" aria-label="The Brighter Living Hour with Dan Kessop">
      <text class="word-blush word-light" x="420" y="400" font-size="44" letter-spacing="14">THE</text>
      <rect class="rule" x="560" y="382" width="520" height="6"/>

      <text class="word-white" x="416" y="570" font-size="170" textLength="664" lengthAdjust="spacingAndGlyphs">BRIGHTER</text>
      <text class="word-white" x="416" y="760" font-size="170" textLength="664" lengthAdjust="spacingAndGlyphs">LIVING</text>

      <text class="word-white" x="420" y="870" font-size="80" textLength="190" lengthAdjust="spacingAndGlyphs">HOUR</text>
      <text class="word-blush word-light" x="640" y="866" font-size="40" textLength="84" lengthAdjust="spacingAndGlyphs">WITH</text>
      <text class="word-blush" x="744" y="868" font-size="60" textLength="336" lengthAdjust="spacingAndGlyphs">DAN KESSOP</text>
    </svg>
  </main>
</body>
</html>
```